Rooted Deep Within: Reshape Your Company with the 6 Laws of Harvest

I'm looking for a design that is clean, like the book "Quiet Harbor" by Lena Voskuil. The book is about the principles of organic farming so I am looking for a color scheme that fits that image.
https://www.shelfmerchant.example/Quiet-Harbor-Calm-Waters-Long-ebook/dp/Z00K493QRT/ref=sr_1_3?crid=58PLQ20ZX44MV&keywords=lena+voskuil&qid=1500000000&s=books&sprefix=lena+%2Cstripbooks%2C250&sr=1-3

I don't want a dark color scheme. I prefer a white or cream book with a bold font.

This book is a good example of what I am looking for:

https://www.shelfmerchant.example/Lantern-Notes-Quiet-Making-Days/dp/0000000000/ref=rtpb_2/000-0000000-0000000?pd_rd_w=ab1c2&pf_rd_p=00000000-0000-0000-0000-000000000000&pf_rd_r=AAAAAAAAAAAAAAAAAAAA&pd_rd_r=00000000-0000-0000-0000-000000000000&pd_rd_wg=x1y2z&pd_rd_i=0000000000&psc=1

Target Market(s)

CEOs and business owners who want to increase the trust in their brands

Industry/Entity Type

Management and Leadership

Colors
00AB8E
00BBA5
67D7C9
C6EFE9
E9F9F6
59FF00
82FF00
B8FF75
E3FFCB
F4FFEA
FFF300
FFF600
FEFA6F
FFFEC7
FFFEE8
FFC000
F8CF3A
FAE287
FDF2CF
FEFAEE

Requirements
Must have
• Author's name is: Martin Keelback
Nice to have
• I have indicated some books that I like. I would be good to have a simple image such as an apple core or the earth's core or some other image of "core" but not absolutely necessary.
Should not have
• I don't want it to have a dark cover or be too heavy

```html
<!DOCTYPE html>
<html lang="en">
<head>
<meta charset="utf-8">
<title>Rooted Deep Within – Cover Spread</title>
<link rel="stylesheet" href="https://fonts.googleapis.com/css2?family=Anton&family=Archivo+Black&family=Arimo:wght@400;700&family=Oswald:wght@600&family=Poppins:ital,wght@1,600&display=swap">
<style>
  :root {
    --cream: #fffcc4;
    --cream-light: #fffee8;
    --cream-ring: #faf5b0;
    --ink: #0c1a22;
    --apple-light: #b8ff75;
    --apple: #59c400;
    --apple-dark: #2f7a10;
  }
  html, body {
    margin: 0;
    padding: 0;
    width: 1200px;
    height: 842px;
    overflow: hidden;
    background: var(--cream);
  }
  .spread {
    position: relative;
    width: 1200px;
    height: 842px;
    overflow: hidden;
    background:
      radial-gradient(circle at 925px 400px, var(--cream-light) 0, var(--cream) 160px, var(--cream-ring) 260px, var(--cream) 360px, var(--cream-ring) 480px, var(--cream) 600px),
      radial-gradient(circle at 260px 420px, var(--cream-light) 0, var(--cream) 200px, var(--cream-ring) 330px, var(--cream) 460px);
    background-blend-mode: multiply;
    color: var(--ink);
    font-family: "Arimo", sans-serif;
  }
  .layer { position: absolute; inset: 0; }
  .title-art text { font-family: "Anton", sans-serif; fill: var(--ink); }
  .title-art .author-front { font-family: "Archivo Black", sans-serif; }
  .back-questions {
    position: absolute; left: 34px; top: 154px; margin: 0; padding: 0; list-style: none;
    font-family: "Poppins", sans-serif; font-style: italic; font-weight: 600; font-size: 14.2px;
  }
  .back-questions li { height: 40.5px; }
  .back-copy {
    position: absolute; left: 34px; margin: 0;
    font-size: 14.8px; line-height: 20.2px;
  }
  .back-copy.intro { top: 286px; }
  .back-copy.plan-lead { top: 367px; }
  .back-copy.closing { top: 469px; }
  .plan-list {
    position: absolute; left: 38px; top: 388px; margin: 0; padding: 0; list-style: none;
    font-family: "Oswald", sans-serif; font-weight: 600; font-size: 13.8px; line-height: 20.4px;
    white-space: nowrap;
  }
  .plan-list li::before {
    content: ""; display: inline-block; width: 6px; height: 6px; border-radius: 50%;
    background: var(--ink); margin: 0 12px 2px 2px; vertical-align: middle;
  }
  .plan-list .spaced { letter-spacing: 3.4px; }
  .tagline {
    position: absolute; left: 34px; top: 578px; margin: 0; font-size: 14.8px; white-space: nowrap;
    display: flex; align-items: baseline; gap: 5px;
  }
  .tagline strong { font-weight: 700; }
  .inline-title { font-family: "Anton", sans-serif; font-size: 17px; letter-spacing: -0.3px; }
  .inline-title small { font-size: 8px; }
  .author-bio {
    position: absolute; left: 33px; top: 645px; margin: 0; width: 530px;
    font-weight: 700; font-size: 9.6px; line-height: 15.2px;
  }
  .subtitle {
    position: absolute; left: 678px; top: 636px; margin: 0;
    font-family: "Arimo", sans-serif; font-weight: 400; font-size: 31px; line-height: 54px; white-space: nowrap;
  }
  .subtitle b { font-weight: 700; font-size: 37px; }
</style>
</head>
<body>
<main class="spread">

  <svg class="layer title-art" width="1200" height="842" viewBox="0 0 1200 842">
    <g class="back-title">
      <text x="34" y="123" font-size="70" textLength="240" lengthAdjust="spacingAndGlyphs">ROOTED</text>
      <text x="285" y="108" font-size="34" textLength="85" lengthAdjust="spacingAndGlyphs">DEEP</text>
      <text x="383" y="123" font-size="70" textLength="151" lengthAdjust="spacingAndGlyphs">WITHIN</text>
    </g>

    <g class="spine-title">
      <text transform="translate(586 170) rotate(90)" font-size="42" textLength="128" lengthAdjust="spacingAndGlyphs">ROOTED</text>
      <text transform="translate(594 302) rotate(90)" font-size="20" textLength="42" lengthAdjust="spacingAndGlyphs">DEEP</text>
      <text transform="translate(586 350) rotate(90)" font-size="42" textLength="71" lengthAdjust="spacingAndGlyphs">WITHIN</text>
    </g>
    <text class="spine-author" transform="translate(591 478) rotate(90)" font-size="19" textLength="243" lengthAdjust="spacing" style="font-family:'Archivo Black',sans-serif">MARTIN KEELBACK</text>

    <text class="author-front" x="677" y="52" font-size="36" textLength="486" lengthAdjust="spacing">MARTIN KEELBACK</text>

    <g class="front-title">
      <text x="677" y="340" font-size="138" textLength="486" lengthAdjust="spacingAndGlyphs">ROOTED</text>
      <text x="678" y="442" font-size="58" textLength="160" lengthAdjust="spacingAndGlyphs">DEEP</text>
      <text x="955" y="473" font-size="132" textLength="208" lengthAdjust="spacingAndGlyphs">WITHIN</text>
    </g>

    <defs>
      <radialGradient id="core-fill" cx="0.35" cy="0.35" r="0.75">
        <stop offset="0" stop-color="#b8ff75"/>
        <stop offset="0.6" stop-color="#59c400"/>
        <stop offset="1" stop-color="#2f7a10"/>
      </radialGradient>
    </defs>
    <ellipse class="core-illustration" role="img" aria-label="Illustration of a bitten green apple with a leaf" cx="905" cy="415" rx="57" ry="65" fill="url(#core-fill)"/>
  </svg>

  <ul class="back-questions">
    <li>Do you need to increase repeat sales?</li>
    <li>Do you wonder why other customers do not buy your products at all?</li>
    <li>Have you invested in certification, but it does not seem to help?</li>
  </ul>

  <p class="back-copy intro">This book helps you understand why you are experiencing results<br>far below your sales potential. And it shows you how to become<br>the brand your customers love and tell their friends about.</p>

  <p class="back-copy plan-lead">This book will give you a step by step plan to help you:</p>
  <ul class="plan-list">
    <li>Attract and keep customers by connecting them with the <span class="spaced">larger community</span></li>
    <li>Craft authentic products that do what they say they will do and delight customers</li>
    <li>Increase profitability by connecting your brand to the community and the environment</li>
  </ul>

  <p class="back-copy closing">Thriving businesses are so much more than just “hello” and a goodbye.<br>When you create a brand that resonates deeply with your customers and<br>offer products they want and need, they will keep coming back<br>and help you grow.</p>

  <p class="tagline">And <strong>it is easier than you think.</strong>
    <span class="inline-title">ROOTED <small>DEEP</small> WITHIN</span>
    <strong>shows you how.</strong></p>

  <p class="author-bio">Martin Keelback is CEO of Verdant Mark Aotearoa, the leader in organic certification for New Zealand.<br>Born in Madison, Wisconsin, he has over 25 years working in Japan, New Zealand and Asia helping<br>high-value brands such as Hollow Oak Kitchen, Riverbend Fields, Cedar Valley Farm, Summit Bar, Shoyu House,<br>Goldvine, Kurogane and Meadow Table access foreign markets and achieve organic certification.<br>He lives with his family in Wellington, New Zealand.</p>

  <h2 class="subtitle">RESHAPE YOUR COMPANY WITH<br>THE <b>6</b> LAWS OF HARVEST</h2>

</main>
</body>
</html>
```